Irrigation Business needs their business cards modernised and revamped

I would like to keep my current logo, colours and revamp the format of the card.

I would like the card to be clean yet important.

Im not sure if you include texture but i would like the named logo to be indented into the card etc.

show me something alive and free something thats clinical to the point yet has a feel of achievement. i would like people to go nice card.

Target Market(s)

high end clients, corporate, sports field manger, the guys that make the decisions

Industry/Entity Type

Business

Contact Information for Business Card

nformation to be included

Dean Harlow (Director)
0487305526
dean@kolvat.biz
www.kestonfieldworks.com

instagram logo
google logo
facebook logo

Colors

Designer to choose colors to be used in the design.

Requirements
Nice to have
• indentations a really nice feel to the card good texture

```html
<!DOCTYPE html>
<html lang="en">
<head>
<meta charset="utf-8">
<title>Keston Fieldworks – Business Card</title>
<link rel="stylesheet" href="https://fonts.googleapis.com/css2?family=Source+Sans+3:wght@400;600;700&display=swap">
<style>
  :root {
    --backdrop: #2e2926;
    --card: #0c0c0d;
    --card-edge: #1a1a1b;
    --brand-light: #2fa6db;
    --brand-deep: #2b6cc0;
    --accent-line: #1f6f93;
    --text-white: #f2f2f2;
    --text-grey: #b9b9b9;
    --silver: #c8c8c8;
  }
  * { box-sizing: border-box; margin: 0; padding: 0; }
  html, body {
    width: 1200px; height: 900px; overflow: hidden;
    background: var(--backdrop);
    font-family: "Source Sans 3", "Myriad Pro", sans-serif;
  }
  .canvas {
    position: relative; width: 1200px; height: 900px;
    display: flex; align-items: center; justify-content: center; gap: 50px;
  }
  .card {
    position: relative; width: 525px; height: 300px;
    background: var(--card);
    border: 1px solid var(--card-edge);
    box-shadow: 0 10px 28px rgba(0,0,0,.45);
  }

  /* Contact side */
  .card--contact .brand-mark {
    position: absolute; left: 52px; top: 58px;
    display: flex; flex-direction: column; align-items: center; gap: 14px;
  }
  .brand-mark__disc {
    width: 150px; height: 150px; border-radius: 50%;
    background: var(--brand-light);
  }
  .brand-mark__name {
    color: var(--brand-light); font-weight: 600; font-size: 13px; letter-spacing: 2px;
  }
  .divider {
    position: absolute; left: 262px; top: 58px; width: 1px; height: 150px;
    background: var(--accent-line);
  }
  .person { position: absolute; left: 282px; top: 68px; }
  .person__name {
    color: var(--brand-light); font-weight: 600; font-size: 19px; letter-spacing: .5px;
    text-transform: uppercase; line-height: 1;
  }
  .person__role { color: var(--text-grey); font-size: 13px; margin-top: 2px; }
  .contact-list { list-style: none; margin-top: 26px; }
  .contact-list li {
    display: flex; align-items: center; gap: 7px;
    color: var(--text-white); font-size: 14.5px; line-height: 21px;
  }
  .contact-list svg { width: 13px; height: 13px; flex: none; }

  /* Brand side */
  .card--brand { display: flex; flex-direction: column; align-items: center; }
  .card--brand .brand-disc {
    margin-top: 48px; width: 78px; height: 78px; border-radius: 50%;
    background: var(--silver);
  }
  .brand-name {
    margin-top: 20px; color: var(--silver); font-weight: 700; font-size: 34px;
    letter-spacing: 1px; text-transform: uppercase; line-height: 1;
  }
  .social { display: flex; gap: 6px; margin-top: 16px; }
  .social span {
    width: 18px; height: 18px; border-radius: 50%; background: var(--text-white);
  }
  .base-rule {
    position: absolute; left: 50%; bottom: 46px; transform: translateX(-50%);
    width: 300px; height: 1px; background: var(--accent-line);
  }
</style>
</head>
<body>
<main class="canvas">

  <section class="card card--contact" aria-label="Contact side of business card">
    <div class="brand-mark">
      <div class="brand-mark__disc"></div>
      <span class="brand-mark__name">KESTON FIELDWORKS</span>
    </div>
    <div class="divider"></div>
    <div class="person">
      <h1 class="person__name">Dean Harlow</h1>
      <p class="person__role">Director</p>
      <ul class="contact-list">
        <li>
          <svg viewBox="0 0 14 14" aria-hidden="true"><circle cx="7" cy="7" r="7" fill="var(--brand-light)"/><path d="M4.3 3.6l1.4-.4.8 1.8-.9.7c.4.9 1 1.5 1.9 1.9l.7-.9 1.8.8-.4 1.4c-3 .2-5.5-2.3-5.3-5.3z" fill="#0c0c0d"/></svg>
          0487305526
        </li>
        <li>
          <svg viewBox="0 0 14 14" aria-hidden="true"><circle cx="7" cy="7" r="7" fill="var(--brand-light)"/><rect x="3.6" y="4.6" width="6.8" height="4.8" fill="#0c0c0d"/><path d="M3.8 4.8L7 7.4l3.2-2.6" stroke="var(--brand-light)" stroke-width=".8" fill="none"/></svg>
          dean@kolvat.biz
        </li>
        <li>
          <svg viewBox="0 0 14 14" aria-hidden="true"><circle cx="7" cy="7" r="7" fill="var(--brand-light)"/><circle cx="7" cy="7" r="3.6" fill="none" stroke="#0c0c0d" stroke-width="1"/><path d="M3.4 7h7.2M7 3.4c-1.6 2-1.6 5.2 0 7.2M7 3.4c1.6 2 1.6 5.2 0 7.2" stroke="#0c0c0d" stroke-width=".8" fill="none"/></svg>
          www.kestonfieldworks.com
        </li>
      </ul>
    </div>
  </section>

  <section class="card card--brand" aria-label="Brand side of business card">
    <div class="brand-disc"></div>
    <h2 class="brand-name">Keston Fieldworks</h2>
    <div class="social" aria-label="Social links">
      <span></span><span></span><span></span>
    </div>
    <div class="base-rule"></div>
  </section>

</main>
</body>
</html>
```